Website for software company "velora"

We need a website for our software company/startup named "velora". We are developing several products (currently 3 standard-software products) which are all in different sectors, but all our products are available for Laptops/PC/Mobile Phones/Tablets, ... We do also create custom software and support our customers with consulting to optimize their processes.
We already have a Logo which you can find in the attached files.
We are a young team of 4 members (two founders and 2 employees).

To get an idea of our products -> the first one is a planning software for healthcare organizations (eg. BlueHaven, firebrigade, pharmacy), the second one is a booking software for sport clubs and the third one is a competition software for sports hunting. You see very diverse. Include or ignore this info of our products as you like.

The design has to be a bootstrap 4 (or higher) design. We have licenced FontAwesome as iconset. Responsive design should come without saying.

• Starting page, product pages, news section, contact, team, services

```html
<!DOCTYPE html>
<html lang="en">
<head>
<meta charset="utf-8">
<title>velora — Software Company</title>
<link href="https://fonts.googleapis.com/css2?family=Montserrat:wght@400;500;600;700;800&display=swap" rel="stylesheet">
<style>
:root{
  --orange:#f4843a;
  --orange-soft:rgba(244,132,58,.45);
  --dark:#2f353b;
  --ink:#222;
  --text:#444;
  --muted:#666;
  --light:#f3f3f4;
  --footer:#0b0b0b;
  --white:#fff;
}
*{box-sizing:border-box;margin:0;padding:0}
html,body{width:1200px;height:4104px;overflow:hidden}
body{position:relative;background:var(--white);font-family:'Montserrat',sans-serif;color:var(--text)}
.abs{position:absolute}
a{color:inherit;text-decoration:none}

/* header */
.site-header{position:absolute;left:0;top:0;width:1200px;height:85px;background:var(--white);z-index:5}
.brand{position:absolute;font-weight:800;letter-spacing:1px;color:var(--dark);text-transform:uppercase}
.header-brand{left:112px;top:12px;font-size:54px;line-height:60px}
.main-nav{position:absolute;top:30px;left:0;font-size:15px;color:#333}
.main-nav a{position:absolute;white-space:nowrap}
.main-nav .active{color:var(--orange)}
.btn-login{position:absolute;left:955px;top:14px;width:132px;height:54px;border-radius:27px;background:var(--orange);color:#fff;font-weight:700;font-size:16px;text-align:center;line-height:54px}

/* hero */
.hero{position:absolute;left:0;top:85px;width:1200px;height:730px}
.hero-copy{position:absolute;left:131px;top:197px;color:#fff}
.hero-copy .kicker{font-weight:700;font-size:21px;line-height:26px;letter-spacing:.5px}
.hero-copy .hero-brand{font-weight:800;font-size:64px;line-height:78px;letter-spacing:2px;text-transform:uppercase}
.hero-copy p{font-size:15.5px;line-height:26px;width:310px;margin-top:2px}
.btn-start{position:absolute;left:131px;top:382px;width:153px;height:64px;border-radius:32px;background:#fff;color:var(--orange);font-weight:700;font-size:15px;text-align:center;line-height:64px}
.social-rail{position:absolute;left:36px;top:177px;width:28px}
.social-rail .dot{display:block;width:14px;height:14px;border-radius:50%;background:#555;margin:0 auto 11px}
.social-rail .dot.ring{width:26px;height:26px;background:none;border:1.5px solid #555}
.social-rail .rule{width:1px;height:70px;background:#777;margin:6px auto}
.scroll-label{position:absolute;left:44px;top:435px;font-size:9px;color:#555;transform:rotate(-90deg);transform-origin:left top;white-space:nowrap;letter-spacing:.5px}

/* about */
.eyebrow{font-weight:700;font-size:14px;color:var(--ink);padding-left:13px;border-left:3px solid var(--orange);line-height:14px}
.about-title{position:absolute;left:112px;top:888px;font-size:31px;line-height:45px;color:var(--ink);font-weight:400}
.about-title b{font-weight:700}
.about-text{position:absolute;left:545px;top:866px;width:544px;font-size:14.5px;line-height:25.5px;text-align:justify;color:#555}
.learn-more{position:absolute;left:545px;top:1008px;height:36px;width:38px;border:2px solid var(--orange);border-right:none}
.learn-more span{position:absolute;left:20px;top:8px;white-space:nowrap;font-weight:600;font-size:14px;color:var(--ink)}
.learn-more span i{color:var(--orange);font-style:normal}

.photo{position:absolute}
.frame{position:absolute;left:91px;top:1098px;width:558px;height:250px;border:5px solid var(--orange)}
.mission{position:absolute;left:115px;top:1496px;width:460px;border-left:2px solid var(--orange);padding-left:10px}
.mission h4{font-size:14px;font-weight:700;color:var(--ink);margin-bottom:12px}
.mission p{font-size:14.5px;line-height:25.5px;color:#555}
.dots{position:absolute;left:900px;top:1555px;width:260px;height:125px}

/* software */
.software{position:absolute;left:0;top:1769px;width:1200px;height:686px;background:linear-gradient(180deg,#e9eaeb,#f6f6f7 60%,#eeeeef)}
.section-title{position:absolute;left:0;width:1200px;text-align:center;font-size:31px;color:var(--ink);font-weight:400}
.section-title b{font-weight:700}
.product-card{position:absolute;border:1px solid #aaa;border-radius:10px;background:rgba(255,255,255,.25);text-align:center}
.product-card.featured{background:#fff;border:none;box-shadow:0 10px 30px rgba(0,0,0,.15);overflow:hidden}
.icon-badge{position:absolute;width:102px;height:102px;border-radius:50%;background:var(--orange);box-shadow:0 0 0 6px rgba(244,132,58,.25)}
.product-card h3{position:absolute;left:0;width:100%;font-size:19px;font-weight:600;color:var(--ink)}
.product-card p{position:absolute;left:0;width:100%;font-size:15px;line-height:25.5px;color:#444}
.product-card .more{position:absolute;left:0;width:100%;font-size:15px;font-weight:600;color:var(--orange)}

/* testimonials */
.testimonial-card{position:absolute;width:349px;height:243px;background:#fff;box-shadow:0 6px 24px rgba(0,0,0,.1);padding:28px 20px 0 22px}
.testimonial-card::before{content:"";position:absolute;left:-8px;top:-8px;width:150px;height:80px;border-top:8px solid var(--orange);border-left:8px solid var(--orange)}
.testimonial-card h4{font-size:26px;font-weight:500;color:var(--ink)}
.testimonial-card .role{font-size:15px;color:#555;margin-top:4px}
.testimonial-card blockquote{font-size:14.5px;line-height:25.5px;color:#555;margin-top:20px}
.quote-mark{position:absolute;font-size:110px;line-height:110px;font-weight:700;color:rgba(244,132,58,.55)}

/* news */
.news{position:absolute;left:0;top:3111px;width:1200px;height:730px;background:linear-gradient(180deg,#ededee,#f7f7f8)}
.news-card{position:absolute;width:311px;height:340px;background:#fff;box-shadow:0 6px 24px rgba(0,0,0,.1)}
.news-card .thumb{position:absolute;left:16px;top:-24px;width:279px;height:175px}
.news-card .date{position:absolute;left:16px;top:178px;font-size:14px;color:var(--orange);font-weight:500}
.news-card h3{position:absolute;left:16px;top:206px;width:285px;font-size:20px;line-height:32px;font-weight:600;color:var(--ink)}
.news-card p{position:absolute;left:16px;top:276px;font-size:14.5px;color:#555}
.news-card .arrow{position:absolute;right:14px;top:308px}

/* footer */
.footer-brand{left:112px;top:3850px;font-size:62px;line-height:66px;color:#fff}
.footer-social{position:absolute;top:3952px;left:112px}
.footer-social span{position:absolute;top:0;width:40px;height:40px;border-radius:50%;border:2px solid #fff}
.footer-col{position:absolute;top:3836px;color:#fff}
.footer-col h5{font-size:20px;font-weight:500;margin-bottom:12px;letter-spacing:.3px}
.footer-col li{list-style:none;font-size:15px;line-height:25.5px}
.contact-row{position:absolute;left:862px;font-size:15px;line-height:25.5px;color:#fff;padding-left:28px}
.contact-row svg{position:absolute;left:0;top:5px}
.copyright{position:absolute;left:0;top:4054px;width:1200px;text-align:center;font-size:14px;color:#fff}
</style>
</head>
<body>

<header class="site-header">
  <div class="brand header-brand">velora</div>
  <nav class="main-nav">
    <a class="active" style="left:440px">Home</a>
    <a style="left:532px">About</a>
    <a style="left:623px">Software</a>
    <a style="left:735px">Blog</a>
    <a style="left:815px">Contact</a>
  </nav>
  <svg class="abs" style="left:459px;top:12px" width="12" height="16"><path d="M1 1 L11 8 L1 15Z" fill="#bbb"/></svg>
  <a class="btn-login">LOG IN</a>
</header>

<section class="hero">
  <svg width="1200" height="730" style="position:absolute;left:0;top:0">
    <defs>
      <linearGradient id="heroPhoto" x1="0" y1="0" x2="1" y2="1">
        <stop offset="0" stop-color="#d9dadc"/>
        <stop offset=".5" stop-color="#8f8f93"/>
        <stop offset="1" stop-color="#3b3e48"/>
      </linearGradient>
    </defs>
    <rect x="0" y="0" width="1200" height="730" fill="url(#heroPhoto)" role="img" aria-label="Photo of two businessmen talking at a desk with a laptop"/>
    <polygon points="255,0 545,0 700,150 410,150" fill="var(--orange)"/>
    <polygon points="690,0 870,0 870,170 770,170" fill="var(--orange)"/>
    <polygon points="112,3 510,305 112,615" fill="var(--dark)"/>
    <polygon points="0,600 845,697 1200,628 1200,730 0,730" fill="var(--orange)"/>
    <polygon points="0,612 845,720 1200,638 1200,730 0,730" fill="#fff"/>
  </svg>
  <div class="social-rail">
    <span class="dot ring"></span><span class="dot"></span><span class="dot"></span><span class="dot"></span>
    <div class="rule"></div>
  </div>
  <div class="scroll-label">SCROLL DOWN</div>
  <svg class="abs" style="left:43px;top:445px" width="16" height="30"><circle cx="8" cy="6" r="5" fill="var(--orange)"/><path d="M8 10 V27 M3 22 L8 27 L13 22" stroke="#555" stroke-width="1.5" fill="none"/></svg>
  <div class="hero-copy">
    <div class="kicker">WELCOME TO</div>
    <div class="hero-brand">velora</div>
    <p>Lorem ipsum dolor sit amet, consectetur adipiscing elit, sed do eiusmod tempor</p>
  </div>
  <a class="btn-start">GET STARTED</a>
</section>

<section class="about">
  <div class="eyebrow abs" style="left:112px;top:866px">ABOUT US</div>
  <h2 class="about-title">IN <b>VELORA</b><br>OUR <b>SOFTWARE</b><br>COMPANY</h2>
  <p class="about-text">Lorem ipsum dolor sit amet, consectetur adipiscing elit, sed do eiusmod tempor incididunt ut labore et dolore magna aliqua. Ut enim ad minim veniam, quis nostrud exercitation ullamco laboris nisi ut aliquip ex ea commodo consequat. Duis aute irure dolor in reprehenderit in voluptate velit esse cillum dolore eu fugiat nulla pariatur.</p>
  <a class="learn-more"><span>LEARN MORE <i>&rarr;</i></span></a>

  <div class="frame"></div>
  <div class="photo" style="left:112px;top:1119px;width:714px;height:330px;background:linear-gradient(120deg,#1e3c6e,#2f5d9c 45%,#152238)" role="img" aria-label="Photo of developers working at computer monitors in an office"></div>
  <div class="photo" style="left:642px;top:1310px;width:447px;height:328px;background:linear-gradient(160deg,#e8ecef,#b9bfc4 55%,#6f6a63);box-shadow:0 8px 24px rgba(0,0,0,.2)" role="img" aria-label="Photo of a woman coding at a desk in a bright office"></div>
  <svg class="dots" viewBox="0 0 260 125">
    <g fill="#222">
      <circle cx="205" cy="5" r="2.5"/><circle cx="230" cy="5" r="2.5"/><circle cx="255" cy="5" r="2.5"/>
      <circle cx="205" cy="28" r="2.5"/><circle cx="230" cy="28" r="2.5"/><circle cx="255" cy="28" r="2.5"/>
      <circle cx="205" cy="51" r="2.5"/><circle cx="230" cy="51" r="2.5"/><circle cx="255" cy="51" r="2.5"/>
      <circle cx="5" cy="74" r="2.5"/><circle cx="30" cy="74" r="2.5"/><circle cx="55" cy="74" r="2.5"/><circle cx="80" cy="74" r="2.5"/><circle cx="105" cy="74" r="2.5"/><circle cx="130" cy="74" r="2.5"/><circle cx="155" cy="74" r="2.5"/><circle cx="180" cy="74" r="2.5"/><circle cx="205" cy="74" r="2.5"/><circle cx="230" cy="74" r="2.5"/><circle cx="255" cy="74" r="2.5"/>
      <circle cx="5" cy="97" r="2.5"/><circle cx="30" cy="97" r="2.5"/><circle cx="55" cy="97" r="2.5"/><circle cx="80" cy="97" r="2.5"/><circle cx="105" cy="97" r="2.5"/><circle cx="130" cy="97" r="2.5"/><circle cx="155" cy="97" r="2.5"/><circle cx="180" cy="97" r="2.5"/><circle cx="205" cy="97" r="2.5"/><circle cx="230" cy="97" r="2.5"/><circle cx="255" cy="97" r="2.5"/>
      <circle cx="5" cy="120" r="2.5"/><circle cx="30" cy="120" r="2.5"/><circle cx="55" cy="120" r="2.5"/><circle cx="80" cy="120" r="2.5"/><circle cx="105" cy="120" r="2.5"/><circle cx="130" cy="120" r="2.5"/><circle cx="155" cy="120" r="2.5"/><circle cx="180" cy="120" r="2.5"/><circle cx="205" cy="120" r="2.5"/><circle cx="230" cy="120" r="2.5"/><circle cx="255" cy="120" r="2.5"/>
    </g>
  </svg>
  <div class="mission">
    <h4>OUR MISSION</h4>
    <p>Lorem ipsum dolor sit amet, consectetur adipiscing elit, sed do eiusmod tempor incididunt ut labore et dolore magna aliqua. Ut enim ad minim veniam, quis nostrud exercitation</p>
  </div>
</section>

<section class="software">
  <svg width="1200" height="686" style="position:absolute;left:0;top:0">
    <polygon points="327,30 480,170 480,645 327,645" fill="var(--orange-soft)"/>
    <polygon points="718,60 873,60 873,655 790,600 718,600" fill="var(--orange-soft)"/>
  </svg>
  <h2 class="section-title" style="top:72px">Our <b>Software</b></h2>

  <article class="product-card" style="left:112px;top:153px;width:312px;height:346px">
    <div class="icon-badge" style="left:105px;top:35px"></div>
    <svg class="abs" style="left:136px;top:66px" width="40" height="40" viewBox="0 0 40 40" fill="none" stroke="#fff" stroke-width="2.2"><path d="M4 22 V34 H14 L20 30 M36 22 V34 H26 L20 30"/><path d="M20 8 a6 6 0 0 1 10 6 L20 24 L10 14 a6 6 0 0 1 10-6Z"/><path d="M20 12 v7 M16.5 15.5 h7"/></svg>
    <h3 style="top:163px">Healthcare Organizations</h3>
    <p style="top:200px">Lorem ipsum dolor sit amet,<br>consectetur adipiscing elit, sed<br>do eiusmod tempor incididunt.</p>
    <div class="more" style="top:294px">Learn More</div>
  </article>

  <article class="product-card featured" style="left:445px;top:153px;width:310px;height:453px">
    <div style="position:absolute;left:0;top:0;width:310px;height:230px;background:linear-gradient(180deg,#b9d3ea,#6f9a4c 55%,#3d6b2c)" role="img" aria-label="Photo of a golfer carrying a bag on a green course"></div>
    <div class="icon-badge" style="left:104px;top:171px"></div>
    <svg class="abs" style="left:135px;top:202px" width="40" height="40" viewBox="0 0 40 40" fill="none" stroke="#fff" stroke-width="2.2"><ellipse cx="20" cy="20" rx="16" ry="11" transform="rotate(-30 20 20)"/><path d="M10 28 L30 12 M15 18 l4 4 M19 15 l4 4 M23 12 l4 4"/></svg>
    <h3 style="top:302px">Sport Clubs</h3>
    <p style="top:339px">Lorem ipsum dolor sit amet,<br>consectetur adipiscing elit, sed</p>
    <div class="more" style="top:408px">Learn More</div>
  </article>

  <article class="product-card" style="left:776px;top:153px;width:313px;height:346px">
    <div class="icon-badge" style="left:105px;top:35px"></div>
    <svg class="abs" style="left:136px;top:66px" width="40" height="40" viewBox="0 0 40 40" fill="none" stroke="#fff" stroke-width="2.2"><circle cx="20" cy="20" r="13"/><circle cx="20" cy="20" r="6"/><circle cx="20" cy="20" r="1.5" fill="#fff"/><path d="M20 2 V10 M20 30 V38 M2 20 H10 M30 20 H38"/></svg>
    <h3 style="top:163px">Sports Hunting</h3>
    <p style="top:200px">Lorem ipsum dolor sit amet,<br>consectetur adipiscing elit, sed<br>do eiusmod tempor incididunt.</p>
    <div class="more" style="top:294px">Learn More</div>
  </article>
</section>

<section class="testimonials">
  <h2 class="section-title" style="top:2533px">Our <b>Testimonials</b></h2>

  <div class="photo" style="left:112px;top:2638px;width:282px;height:300px;background:linear-gradient(180deg,#2a2a2a,#111)" role="img" aria-label="Portrait photo of a man in a dark suit"></div>
  <div class="quote-mark" style="left:470px;top:2668px">&ldquo;</div>
  <article class="testimonial-card" style="left:241px;top:2781px">
    <h4>Daniel Marsh</h4>
    <div class="role">Lorem ipsum dolor</div>
    <blockquote>"Lorem ipsum dolor sit amet, co adipiscing elit, sed do eiusmod incididunt incididunt ut labore et dolore magn labore et dolore magna laborum."</blockquote>
  </article>

  <div class="photo" style="left:610px;top:2638px;width:284px;height:300px;background:linear-gradient(180deg,#d9d9d9,#a9a9ab)" role="img" aria-label="Portrait photo of a woman in a dark blazer"></div>
  <div class="quote-mark" style="left:968px;top:2668px">&ldquo;</div>
  <article class="testimonial-card" style="left:740px;top:2781px">
    <h4>Clara Wendt</h4>
    <div class="role">Lorem ipsum dolor</div>
    <blockquote>"Lorem ipsum dolor sit amet, co adipiscing elit, sed do eiusmod incididunt incididunt ut labore et dolore magn labore et dolore magna laborum."</blockquote>
  </article>
</section>

<section class="news">
  <h2 class="section-title" style="top:89px">LATEST <b>NEWS</b></h2>
  <article class="news-card" style="left:112px;top:172px">
    <div class="thumb" style="background:linear-gradient(160deg,#8b6c4a,#c9a15a 55%,#e0b030)" role="img" aria-label="Photo of a smiling woman using a laptop"></div>
    <div class="date">Apr 16, 2022</div>
    <h3>Sed ut perspiciatis unde on is iste natus error sit</h3>
    <p>Lorem ipsum dolor sit amet, conse</p>
    <svg class="arrow" width="26" height="18" viewBox="0 0 26 18" fill="none" stroke="var(--orange)" stroke-width="2.5"><path d="M1 9 H23 M16 2 L23 9 L16 16"/></svg>
  </article>
  <article class="news-card" style="left:445px;top:172px">
    <div class="thumb" style="background:linear-gradient(160deg,#5d6670,#a8afb6 55%,#d6d8da)" role="img" aria-label="Photo of two colleagues discussing at a laptop"></div>
    <div class="date">Apr 16, 2022</div>
    <h3>Sed ut perspiciatis unde on is iste natus error sit</h3>
    <p>Lorem ipsum dolor sit amet, conse</p>
    <svg class="arrow" width="26" height="18" viewBox="0 0 26 18" fill="none" stroke="var(--orange)" stroke-width="2.5"><path d="M1 9 H23 M16 2 L23 9 L16 16"/></svg>
  </article>
  <article class="news-card" style="left:776px;top:172px">
    <div class="thumb" style="background:linear-gradient(160deg,#3a4350,#7b8592 55%,#c8c2b8)" role="img" aria-label="Photo of a man and woman working together at a computer"></div>
    <div class="date">Apr 16, 2022</div>
    <h3>Sed ut perspiciatis unde on is iste natus error sit</h3>
    <p>Lorem ipsum dolor sit amet, conse</p>
    <svg class="arrow" width="26" height="18" viewBox="0 0 26 18" fill="none" stroke="var(--orange)" stroke-width="2.5"><path d="M1 9 H23 M16 2 L23 9 L16 16"/></svg>
  </article>
</section>

<footer class="site-footer">
  <svg width="1200" height="420" style="position:absolute;left:0;top:3684px">
    <polygon points="0,130 840,4 1200,90 1200,420 0,420" fill="var(--orange)"/>
    <polygon points="0,135 845,40 1200,100 1200,420 0,420" fill="var(--footer)"/>
  </svg>
  <div class="brand footer-brand abs">velora</div>
  <div class="footer-social">
    <span style="left:0"></span><span style="left:54px"></span><span style="left:108px"></span><span style="left:162px"></span>
  </div>
  <div class="footer-col" style="left:459px">
    <h5>QUICK LINKS</h5>
    <ul><li>Home</li><li>About</li><li>Software</li><li>Testimonials</li><li>News</li></ul>
  </div>
  <div class="footer-col" style="left:671px">
    <h5>COMPANY</h5>
    <ul><li>Terms&amp;condtions</li><li>Privacy Policy</li><li>About Us</li><li>Support</li></ul>
  </div>
  <div class="footer-col" style="left:862px">
    <h5>CONTACT US</h5>
  </div>
  <div class="contact-row" style="top:3876px">
    <svg width="12" height="16" viewBox="0 0 12 16"><path d="M6 0 a6 6 0 0 1 6 6 c0 4-6 10-6 10 S0 10 0 6 a6 6 0 0 1 6-6Z" fill="#fff"/><circle cx="6" cy="6" r="2.2" fill="var(--footer)"/></svg>
    Lorem ipsum dolor sit amet,<br>consectetur adipiscing elit,
  </div>
  <div class="contact-row" style="top:3938px">
    <svg width="14" height="14" viewBox="0 0 14 14"><path d="M3 0 L5.5 3.5 L4 5.5 C5 7.5 6.5 9 8.5 10 L10.5 8.5 L14 11 L12.5 13.5 C6 13.5 0.5 8 0.5 1.5Z" fill="#fff"/></svg>
    +1(555) 010 0199
  </div>
  <div class="contact-row" style="top:3973px">
    <svg width="15" height="12" viewBox="0 0 15 12"><rect width="15" height="12" fill="#fff"/><path d="M0 0 L7.5 6 L15 0" stroke="var(--footer)" stroke-width="1.5" fill="none"/></svg>
    info@velora.com
  </div>
  <div class="copyright">&copy;Copyrights 2022 velora &nbsp;&nbsp;|&nbsp;&nbsp; All Rights Reserved</div>
</footer>

</body>
</html>
```